Business Cards for IT Consulting Company (Managed Service Provider)

I am looking to have some business cards printed and would like some designs. We are an IT Consulting company based in Vancouver BC. I would like a nice clean and modern look to the cards. I have uploaded all the versions of my logo so parts can be used as needed. Here is a snippit from our website homepage:

Quillbrook Networks Ltd. is an IT Solutions Partner located in Vancouver BC, Canada. We offer IT solutions and support to customers in the greater Vancouver Area. With expertise in Microsoft platforms, as well as Linux and Mac OSX and over 12 years experience in the IT industry, Quillbrook Networks is dedicated to offering our clients top quality service and products. We take pride in the solutions we offer our customers. The greatest compliment a client can give us is to recommend our services.

Quillbrook Networks Ltd. offers a wide range of IT services from onsite service to remote support and managed service solutions. This allows clients to choose the support path that best suits their company’s needs. Supporting many different sized companies from small to enterprise level over the past 12 years Quillbrook Networks has the experience and expertise needed to ensure things run smoothly. Allowing our clients to focus on doing business.

Revolutionizing the way IT services are delivered.

Quillbrook Networks is dedicated to providing our clients with IT solutions that work and grow with them for years to come. This philosophy helps save money in the long run instead of replacing equipment constantly. Far too often IT solutions are not well thought out and while possibly solving the problem at hand, require replacement due to growth or quality within a very short time frame. Quillbrook Networks takes pride in providing solutions that will last and be able to accommodate growth without the need for replacement.

Industry/Entity Type

Information Technology

Contact Information for Business Card

Quillbrook Networks Ltd.
(Employee Name)
Eml: (Employees Email Address)
Web: quillbrook.me
Ph: 604-555-0148

Font styles to use
Serif
Sans Serif

Requirements
Must have
• The Company logo and company colors.
Nice to have
• - Our tag line: "Revolutionizing IT Services" or "Revolutionizing the way IT services are delivered."
• - Also I really like the idea of nature and technology together blending which is sort of where my logo came from so integrating that somehow onto the business cards would be great.

```html
<!DOCTYPE html>
<html lang="en">
<head>
<meta charset="utf-8">
<title>Quillbrook Networks Ltd. – Business Cards</title>
<link href="https://fonts.googleapis.com/css2?family=Raleway:wght@300;400;600;700&display=swap" rel="stylesheet">
<style>
  :root {
    --bg: #cfe9e1;
    --card: #ffffff;
    --brand-blue: #0ea5dd;
    --brand-blue-deep: #0799d3;
    --ink: #3f4448;
    --white: #ffffff;
  }
  * { box-sizing: border-box; margin: 0; padding: 0; }
  html, body {
    width: 1200px; height: 856px; overflow: hidden;
    background: var(--bg);
    font-family: "Raleway", sans-serif;
  }
  .stage { position: relative; width: 1200px; height: 856px; }
  .card {
    position: absolute;
    width: 520px; height: 297px;
    border-radius: 30px;
    background: var(--card);
    overflow: hidden;
    box-shadow: 0 10px 30px rgba(40, 90, 80, 0.18);
  }

  /* Front card: brand + tagline */
  .card--brand { left: 50px; top: 130px; }
  .card--brand .brand {
    position: absolute; left: 0; right: 0; top: 72px;
    display: flex; align-items: center; justify-content: center; gap: 18px;
  }
  .brand-mark {
    width: 50px; height: 50px;
    border: 4px solid var(--brand-blue);
    border-radius: 50%;
    flex: none;
  }
  .brand-name {
    font-weight: 700; font-size: 34px; line-height: 1.05;
    color: var(--brand-blue); letter-spacing: 0.2px;
  }
  .card--brand .brand-name { max-width: 260px; }
  .tagline {
    position: absolute; left: 0; right: 0; top: 196px;
    text-align: center; font-size: 25px; font-weight: 400;
    letter-spacing: 0.3px;
  }
  .tagline__lead { color: var(--brand-blue); }
  .tagline__tail { color: var(--ink); }

  /* Back card: contact */
  .card--contact { left: 630px; top: 430px; }
  .card--contact .panel {
    position: absolute; right: 0; top: 0; bottom: 0; width: 335px;
    background: linear-gradient(180deg, var(--brand-blue) 0%, var(--brand-blue-deep) 100%);
  }
  .card--contact .brand {
    position: absolute; left: 22px; top: 50%; transform: translateY(-50%);
    width: 150px;
    display: flex; align-items: center; gap: 8px;
  }
  .card--contact .brand-mark { width: 22px; height: 22px; border-width: 2px; }
  .card--contact .brand-name { font-size: 15px; line-height: 1.15; }
  .person {
    position: absolute; left: 30px; top: 62px;
    font-size: 28px; font-weight: 300; color: var(--white);
    letter-spacing: 1.5px; text-transform: uppercase;
  }
  .contact-list {
    position: absolute; left: 30px; top: 120px;
    list-style: none;
  }
  .contact-list li {
    display: flex; align-items: center; gap: 12px;
    height: 36px;
    font-size: 16px; font-weight: 400; color: var(--ink);
  }
  .contact-icon {
    width: 26px; height: 26px; border-radius: 50%;
    background: var(--white); flex: none;
    display: flex; align-items: center; justify-content: center;
  }
  .contact-icon svg { width: 15px; height: 15px; fill: var(--brand-blue); stroke: var(--brand-blue); }
</style>
</head>
<body>
<main class="stage">

  <section class="card card--brand" aria-label="Business card front">
    <div class="brand">
      <span class="brand-mark" aria-hidden="true"></span>
      <span class="brand-name">Quillbrook Networks Ltd.</span>
    </div>
    <p class="tagline"><span class="tagline__lead">Revolutionizing</span> <span class="tagline__tail">IT Services</span></p>
  </section>

  <section class="card card--contact" aria-label="Business card back">
    <div class="brand">
      <span class="brand-mark" aria-hidden="true"></span>
      <span class="brand-name">Quillbrook Networks Ltd.</span>
    </div>
    <div class="panel">
      <h1 class="person">Daniel Marsh</h1>
      <ul class="contact-list">
        <li>
          <span class="contact-icon">
            <svg viewBox="0 0 16 16" aria-hidden="true"><path stroke="none" d="M4 1.5 6 1l1.4 3.2-1.3 1a8 8 0 0 0 4.7 4.7l1-1.3L15 10l-.5 2c-.3 1.3-1.7 2-3 1.6A14 14 0 0 1 2.4 4.5C2 3.2 2.7 1.8 4 1.5z"/></svg>
          </span>
          daniel.marsh@quillbrook.me
        </li>
        <li>
          <span class="contact-icon">
            <svg viewBox="0 0 16 16" aria-hidden="true"><rect x="1.5" y="3.5" width="13" height="9" fill="none" stroke-width="1.6"/><path d="M1.5 3.5 8 9l6.5-5.5" fill="none" stroke-width="1.6"/></svg>
          </span>
          quillbrook.me
        </li>
        <li>
          <span class="contact-icon">
            <svg viewBox="0 0 16 16" aria-hidden="true"><g fill="none" stroke-width="1.3"><circle cx="8" cy="8" r="6.5"/><ellipse cx="8" cy="8" rx="3" ry="6.5"/><path d="M1.5 8h13M2.5 5h11M2.5 11h11"/></g></svg>
          </span>
          604-555-0148
        </li>
      </ul>
    </div>
  </section>

</main>
</body>
</html>
```